AMBER AND SLATE WEB

We need a home design in wordpress, we have now a web but we would like to improve it. Our current web is www.amberandslatevillas.example Our business is holliday rental of villas in Ibiza. Our guest must know that we are a reliable company, professional and with experience and good reviews. We want them to click in our reservation engine: https://bookings.amberandslatevillas.example/en/ and make reservation in our website. We would also like to say that all the properties that we have are just us who commercialize so we have best price available. Many people are going to see our villas in staylist.example and look to our website to make a reservation with us so we need to show them that they are at the right place and click at our link to our reservation engine. What make us special is that we are a local company, we are from Ibiza, Our guests are always received in person by the Amber and Slate Ibiza team. You will enjoy extensive tourist information when you check in and during the entire stay. You will be attended by ChatterLine and calls, always happy to help so that you have a happy and fun stay! Our guest stay is better than in hotel as they have more spece, private swiming pool, private garden, barbeque ... To rent a villa is the best way to stay in Ibiza. We also have a promotional video: https://vidshare.example/Qm7TzR2pLxA Let our philosophy be shown, we think that coming on holiday to Ibiza implies seeing the nature that we have in Ibiza, hence our name AMBER AND SLATE, like the pins that almost touch the sea in Ibiza, or the posidonea meadows where the intense green of the seaweed and the blue of the sea. We are aware of the environment, and we love Ibiza. For us, the client who visits Ibiza, should rent a car, go around the island, eat in a restaurant one day in front of the sea, is a night of partying to the discs, go shopping, visit the ancient heritage of Umanity, make some aquatic sport, enjoy the pool, those are for us Ibiza.

Target Market(s)

Europe, people from Holand, UK, Germany, France, Spain ...

Industry/Entity Type

Tourism

Colors

Designer to choose colors to be used in the design.

Requirements
Must have
• Pictures of Ibiza.
Nice to have
• Our name Amber and Slate Ibiza is beacuse in Ibiza there is forest that almost touch the watter of the Mediterranean sea, so you can see green of the forest and blue of the sea and the sky. And also beacause under the watter of the sea there is a plant called Posidonia that is also green please see the picture of posidonia.

```html
<!DOCTYPE html>
<html lang="en">
<head>
<meta charset="utf-8">
<title>Amber and Slate Villas Ibiza</title>
<link href="https://fonts.googleapis.com/css2?family=Roboto:wght@400;500;700&family=Poppins:wght@400;500&display=swap" rel="stylesheet">
<style>
:root{
  --green:#4d7a2c;
  --green-dark:#3f6a23;
  --blue:#2b90cc;
  --blue-light:#3398d6;
  --text:#222;
  --muted:#444;
  --line:#cfcfcf;
  --grey-band:#ebebeb;
  --white:#fff;
  --grad:linear-gradient(90deg,var(--green) 0%,var(--blue) 100%);
}
*{box-sizing:border-box;margin:0;padding:0}
html,body{width:1200px;height:3112px;overflow:hidden;background:var(--white)}
body{font-family:"Roboto",sans-serif;color:var(--text);position:relative}
.abs{position:absolute}

/* header */
.brand{left:90px;top:30px;display:flex;align-items:center;gap:14px}
.brand-dot{width:36px;height:36px;border-radius:50%;background:var(--green)}
.brand-name{font-size:34px;font-weight:500;color:var(--green);letter-spacing:1px}
.lang{left:593px;top:32px;display:flex;align-items:center;gap:8px}
.lang-dot{width:42px;height:42px;border-radius:50%;background:linear-gradient(180deg,#c8283a 0 50%,#2a3f8f 50% 100%)}
.lang-text b{display:block;font-size:17px;font-weight:700}
.lang-text span{font-size:19px}
.pill{top:32px;height:47px;border-radius:24px;background:var(--grad);color:var(--white);font-size:16px;display:flex;align-items:center;justify-content:center;gap:6px}
.nav{right:91px;top:109px;display:flex;gap:31px;font-size:18px;font-weight:500;color:#111}

/* hero */
.hero{left:0;top:160px;width:1200px;height:538px;background:linear-gradient(180deg,#2f5fb6 0%,#1d55b8 35%,#2a9bc7 65%,#3d7a3a 100%)}
.hero-brand{left:0;top:395px;width:1200px;display:flex;justify-content:center;align-items:center;gap:18px}
.hero-brand .brand-dot{background:var(--white);width:44px;height:44px}
.hero-brand .brand-name{color:var(--white);font-size:50px}

/* booking */
.booking{left:90px;top:617px;width:1020px;height:161px;background:var(--white);box-shadow:0 2px 10px rgba(0,0,0,.18)}
.field{height:37px;border:1px solid var(--line);font-family:"Poppins",sans-serif;font-size:12px;color:#444;display:flex;align-items:center;justify-content:space-between;padding:0 10px;box-shadow:0 1px 3px rgba(0,0,0,.08)}
.field svg{width:12px;height:12px;fill:var(--blue)}
.book-btn{left:615px;top:708px;width:225px;height:38px;background:var(--grad);color:var(--white);font-family:"Poppins",sans-serif;font-weight:500;font-size:14px;display:flex;align-items:center;justify-content:center;gap:6px}

/* about */
.video{left:80px;top:874px;width:344px;height:344px;border-radius:50%;border:5px solid var(--blue);border-right-color:var(--green);border-top-color:var(--green);padding:6px}
.video-photo{width:100%;height:100%;border-radius:50%;background:linear-gradient(160deg,#c9d7e3 0%,#b98a72 55%,#7a4a3a 100%);display:flex;align-items:center;justify-content:center}
.play{width:56px;height:40px;border-radius:10px;background:#d9111a;display:flex;align-items:center;justify-content:center}
.about-title{left:473px;top:866px;width:640px;font-size:27px;font-weight:500;line-height:44px;color:var(--blue)}
.about-text{left:472px;top:980px;width:630px;font-size:16.5px;line-height:36px;text-align:justify;color:var(--text)}
.wide-text{left:94px;width:1016px;font-size:16.5px;line-height:36px;color:var(--text)}

/* services */
.card{top:1536px;width:324px;height:285px;border:1px solid #9a9a9a;padding:24px 20px}
.card svg{width:62px;height:62px;stroke:var(--blue);fill:none;stroke-width:2}
.card h3{margin-top:42px;font-size:17px;font-weight:500;color:var(--blue)}
.card p{margin-top:10px;font-size:14px;line-height:31px;color:#333;letter-spacing:.2px}
.arrow svg{width:40px;height:30px;stroke:var(--green-dark);fill:none;stroke-width:2.4}

/* testimonials */
.testi{left:0;top:1918px;width:1200px;height:449px;background:var(--grey-band)}
.testi h2{position:absolute;top:76px;width:100%;text-align:center;font-size:35px;font-weight:400;color:var(--blue)}
.quote{left:157px;top:2065px;width:904px;text-align:center;font-size:16.5px;line-height:31px;color:#222}
.qmark{font-size:34px;color:var(--green);font-family:Georgia,serif;font-style:italic}
.avatar{left:563px;top:2190px;width:92px;height:92px;border-radius:50%;background:linear-gradient(160deg,#d9c3a6,#8b6a4d);box-shadow:0 3px 8px rgba(0,0,0,.3)}
.who{left:671px;top:2226px;font-size:13px;font-weight:500;color:var(--blue)}
.tnav{left:995px;top:2228px;display:flex;gap:2px}
.tnav span{width:12px;height:12px;border-radius:50%;background:var(--green)}

/* call */
.call-intro{left:0;top:2454px;width:1200px;text-align:center;font-size:16.5px;line-height:31px;color:#222}
.call{left:0;top:2528px;width:1200px;display:flex;justify-content:center;align-items:center;gap:16px;font-size:36px;color:var(--blue)}
.call svg{width:32px;height:38px;fill:var(--blue)}
.input{height:42px;background:var(--white);border:1px solid #e3e3e3;border-left:3px solid #ddd;box-shadow:0 2px 4px rgba(0,0,0,.08);font-family:"Poppins",sans-serif;font-size:11px;color:#333;display:flex;align-items:center;gap:6px;padding-left:16px}
.input i{width:8px;height:8px;border-radius:50%;background:#333;display:inline-block}
.talk{left:610px;top:2654px;width:429px;height:42px;background:linear-gradient(180deg,var(--blue) 0%,var(--green) 100%);color:var(--white);font-family:"Poppins",sans-serif;font-weight:500;font-size:13px;display:flex;align-items:center;justify-content:center;gap:8px}

/* footer */
.footer{left:0;top:2790px;width:1200px;height:322px;background:linear-gradient(100deg,var(--green) 10%,var(--blue) 70%)}
.foot-brand{top:82px;left:0;width:1200px;display:flex;justify-content:center;align-items:center;gap:16px}
.foot-brand .brand-dot{background:var(--white);width:44px;height:44px}
.foot-brand .brand-name{color:var(--white);font-size:40px}
.social{position:absolute;top:184px;left:0;width:1200px;display:flex;justify-content:center;gap:6px}
.social span{width:30px;height:30px;border-radius:50%;border:2px solid var(--white)}
.foot-nav{position:absolute;top:240px;width:100%;text-align:center;color:var(--white);font-size:18px;font-weight:500;word-spacing:2px}
.copy{position:absolute;top:287px;width:100%;text-align:center;color:#e8f1f7;font-size:14px}
</style>
</head>
<body>

<header>
  <div class="abs brand"><span class="brand-dot"></span><span class="brand-name">AMBER AND SLATE</span></div>
  <div class="abs lang"><span class="lang-dot" role="img" aria-label="English language flag"></span><div class="lang-text"><b>Language</b><span>English ▾</span></div></div>
  <a class="abs pill" style="left:758px;width:162px">▦ Book Now</a>
  <a class="abs pill" style="left:947px;width:162px">▦ All Properties</a>
  <nav class="abs nav"><span>HOME</span><span>EXPERIENCE</span><span>ABOUT US</span><span>CONTACT US</span><span>SEARCH ⌕</span></nav>
</header>

<section class="abs hero" role="img" aria-label="Ibiza cove with pine forest reaching turquoise water and sailing boats"></section>
<div class="abs hero-brand"><span class="brand-dot"></span><span class="brand-name">AMBER AND SLATE</span></div>

<form class="abs booking">
  <div class="abs field" style="left:20px;top:33px;width:224px">Best Available rate<svg viewBox="0 0 12 12"><rect x="0" y="5" width="12" height="4"/><rect x="0" y="2" width="2" height="8"/></svg></div>
  <div class="abs field" style="left:269px;top:33px;width:226px">Check - In<svg viewBox="0 0 12 12"><rect x="1" y="2" width="10" height="9"/></svg></div>
  <div class="abs field" style="left:525px;top:33px;width:225px">Check - Out<svg viewBox="0 0 12 12"><rect x="1" y="2" width="10" height="9"/></svg></div>
  <div class="abs field" style="left:776px;top:33px;width:226px">Adults<svg viewBox="0 0 12 12"><path d="M6 0 10 5H2zM6 12 2 7h8z"/></svg></div>
  <div class="abs field" style="left:269px;top:91px;width:226px">Kids<svg viewBox="0 0 12 12"><path d="M6 0 10 5H2zM6 12 2 7h8z"/></svg></div>
</form>
<a class="abs book-btn">➤ Book Now</a>

<section>
  <div class="abs video"><div class="video-photo" role="img" aria-label="Promotional video still of friends enjoying an Ibiza evening"><span class="play"><svg width="14" height="16" viewBox="0 0 14 16"><path d="M0 0 14 8 0 16z" fill="#fff"/></svg></span></div></div>
  <h1 class="abs about-title">VILLAS AND THE COUNTRYSIDE The best option to stay in Ibiza</h1>
  <p class="abs about-text">Amber and Slate Villas Ibiza is a company specialized in offering its clients accommodation in Villas on the countryside of Ibiza. Our guests enjoy the rural Ibiza, tranquility, relax, private pool, close to dream beaches and coves, the best restaurants, an unforgettable holiday for family or friends.<br>Every day can be a different experience, beach, restaurant, flea market, disco, hiking, kayaking, horseback riding, shopping, history, boat ride! There is a lot of variety for all budgets!</p>
  <p class="abs wide-text" style="top:1270px">The maximum distances of the island are 41 kilometers from north to south and 15 kilometers from east to west, we always recommend renting a car. Enjoy the freedom to go where you prefer, without depending on schedules or public transportation.</p>
  <p class="abs wide-text" style="top:1381px">Each client is different, both for those who discover Ibiza for the first time and for those who have already been many times, it is a pleasure for us to share our favorite places with our guests and help them to make their experience very special.</p>
</section>

<section>
  <div class="abs arrow" style="left:35px;top:1663px"><svg viewBox="0 0 40 30"><path d="M38 15H3M15 3 3 15l12 12"/></svg></div>
  <article class="abs card" style="left:90px">
    <svg viewBox="0 0 62 62"><rect x="6" y="28" width="50" height="20" rx="4"/><path d="M12 28l6-12h26l6 12"/><circle cx="16" cy="38" r="3"/><circle cx="46" cy="38" r="3"/><path d="M10 48v6h8v-6M44 48v6h8v-6"/></svg>
    <h3>RENT A CAR</h3>
    <p>Sed ut perspiciatis unde omnis iste natus error sit voluptatem accusantium dolorem laudantium, totam rem aperiam</p>
  </article>
  <article class="abs card" style="left:438px">
    <svg viewBox="0 0 62 62"><path d="M30 58V22M30 22c-6-10-16-10-22-4M30 22c6-10 16-10 22-4M30 22c-2-8-10-14-16-14M30 22c2-8 10-14 16-14M6 58c8-8 42-8 50 0"/></svg>
    <h3>GO AROUND THE ISLAND</h3>
    <p>Sed ut perspiciatis unde omnis iste natus error sit voluptatem accusantium dolorem laudantium, totam rem aperiam</p>
  </article>
  <article class="abs card" style="left:787px">
    <svg viewBox="0 0 62 62"><circle cx="31" cy="33" r="24"/><ellipse cx="31" cy="33" rx="11" ry="24"/><path d="M7 33h48M11 21h40M11 45h40"/></svg>
    <h3>NIGHT PARTYING TO THE DISCOS</h3>
    <p>Sed ut perspiciatis unde omnis iste natus error sit voluptatem accusantium dolorem laudantium, totam rem aperiam</p>
  </article>
  <div class="abs arrow" style="left:1130px;top:1663px"><svg viewBox="0 0 40 30"><path d="M2 15h35M25 3l12 12-12 12"/></svg></div>
</section>

<section class="abs testi"><h2>TESTIMONIALS</h2></section>
<span class="abs qmark" style="left:138px;top:2040px">“</span>
<p class="abs quote">At vero eos et accusamus et iusto odio dignissimos ducimus qui blanditiis praesentium voluptatum deleniti atque corrupti quos dolores et quas molestias excepturi sint occaecati cupiditate non provident, similique sunt in culpa qui officia deserunt mollitia animi, id est laborum et dolorum fuga. Et harum quidem rerum facilis est et expedita distinctio.</p>
<span class="abs qmark" style="left:1044px;top:2140px">”</span>
<div class="abs avatar" role="img" aria-label="Guest portrait"></div>
<span class="abs who">- MARLOW</span>
<div class="abs tnav"><span></span><span></span></div>

<section>
  <p class="abs call-intro">We find that a phone chat is always the best way to get things started.<br>But if you can’t talk now,send us your details and we’ll happily call you at a timethat suits you.</p>
  <div class="abs call"><svg viewBox="0 0 32 38"><path d="M6 4c3-2 5-1 6 2l2 6c0 2-2 3-3 4 1 4 4 8 7 10 1-1 2-3 4-2l5 3c2 1 2 4 0 6-4 4-10 3-16-4S2 9 6 4z"/></svg>Call 888 888 8888</div>
  <div class="abs input" style="left:161px;top:2598px;width:431px"><i></i>NAME</div>
  <div class="abs input" style="left:610px;top:2598px;width:429px"><i></i>CONTACT NUMBER</div>
  <div class="abs input" style="left:161px;top:2654px;width:431px"><i></i>BEST TIME TO CALL</div>
  <a class="abs talk">➤ YES, I WANT TO TALK WARDROBES</a>
</section>

<footer class="abs footer">
  <div class="abs foot-brand"><span class="brand-dot"></span><span class="brand-name">AMBER AND SLATE</span></div>
  <div class="social"><span></span><span></span><span></span><span></span></div>
  <div class="foot-nav">HOME &nbsp;| &nbsp;EXPERIENCE &nbsp;| &nbsp;ABOUT US &nbsp;| &nbsp;CONTACT US</div>
  <div class="copy">© 2019 Company Name &nbsp;All right reserved</div>
</footer>

</body>
</html>
```